holloway paving service

Needs to have phone number 0418259730 and email markholloway@brightmail.com.au.
ABN 62318470915
name mark holloway

For all your concreting solutions
Excavation
Exposed & colour concrete
House & shed slabs
Driveways
Landing & steps

Contact Information for Business Card

ph 0418259730
email markholloway@brightmail.com.au.
ABN 62318470915
name mark holloway

```html
<!DOCTYPE html>
<html lang="en">
<head>
<meta charset="utf-8">
<title>Holloway Paving Service – Business Card</title>
<link rel="stylesheet" href="https://fonts.googleapis.com/css2?family=Montserrat:wght@400;500;600&family=Lato:wght@400;700&display=swap">
<style>
  :root {
    --backdrop: #1d1d1e;
    --card: #262627;
    --orange: #f26a1b;
    --white: #f2f2f2;
    --silver: #c9c9c9;
    --grey: #8d8d8d;
    --mark: #b5b5b5;
    --mark-dark: #1b1b1c;
  }
  * { margin: 0; padding: 0; box-sizing: border-box; }
  html, body { width: 1200px; height: 900px; overflow: hidden; background: var(--backdrop); }
  .canvas { position: relative; width: 1200px; height: 900px; }
  .card {
    position: absolute; left: 262px; width: 676px; height: 386px;
    background: var(--card); border-radius: 3px;
    box-shadow: 0 10px 30px rgba(0,0,0,.45);
  }
  .card--front { top: 40px; }
  .card--back { top: 474px; }

  /* front */
  .front-brand {
    position: absolute; left: 150px; top: 112px;
    display: flex; align-items: center; gap: 22px;
  }
  .brand-square { width: 92px; height: 92px; background: var(--mark-dark); }
  .brand-rule { width: 1px; height: 110px; background: var(--grey); }
  .front-wordmark {
    font-family: "Montserrat", sans-serif; font-weight: 500;
    font-size: 24px; letter-spacing: 1px; line-height: 1.15;
    color: var(--silver); text-transform: uppercase; width: 300px;
  }
  .front-phone, .front-abn {
    font-family: "Montserrat", sans-serif; font-size: 17px;
    letter-spacing: 3px; color: var(--grey); margin-top: 6px;
  }
  .front-abn { font-size: 13px; letter-spacing: 2px; margin-top: 4px; }
  .front-web {
    position: absolute; left: 0; right: 0; bottom: 46px; text-align: center;
    font-family: "Lato", sans-serif; font-size: 17px; color: var(--white);
  }
  .accent { color: var(--orange); }

  /* back */
  .back-brand {
    position: absolute; left: 46px; top: 30px; width: 320px;
    font-family: "Montserrat", sans-serif; color: var(--orange);
  }
  .back-wordmark {
    font-weight: 600; font-size: 21px; line-height: 1.15;
    letter-spacing: .5px; text-transform: uppercase;
  }
  .back-phone { font-size: 17px; letter-spacing: 3px; margin-top: 4px; }
  .person { position: absolute; left: 46px; top: 118px; }
  .person-name {
    font-family: "Montserrat", sans-serif; font-weight: 500; font-size: 30px;
    letter-spacing: 1px; color: var(--orange); text-transform: uppercase; line-height: 1.2;
  }
  .person-role { font-family: "Lato", sans-serif; font-size: 17px; color: var(--white); }
  .address {
    position: absolute; left: 46px; top: 190px;
    font-family: "Lato", sans-serif; font-size: 18px; line-height: 1.3;
  }
  .address-suburb { color: var(--orange); }
  .address-city { color: var(--white); }
  .contact-list {
    position: absolute; left: 46px; top: 250px; list-style: none;
    font-family: "Lato", sans-serif; font-size: 18px; color: var(--white); line-height: 1.45;
  }
  .contact-list li { display: flex; align-items: center; gap: 10px; }
  .contact-list svg { width: 12px; height: 12px; flex: none; }
  .back-mark {
    position: absolute; right: 100px; top: 110px; width: 170px; height: 170px;
    background: var(--mark); transform: rotate(45deg);
  }
</style>
</head>
<body>
<main class="canvas">
  <section class="card card--front">
    <div class="front-brand">
      <div class="brand-square"></div>
      <div class="brand-rule"></div>
      <div>
        <div class="front-wordmark">Holloway Paving Service</div>
        <div class="front-phone">0418259730</div>
        <div class="front-abn">ABN 62318470915</div>
      </div>
    </div>
    <p class="front-web">www.<span class="accent">hollowaypaving</span>.com.au</p>
  </section>

  <section class="card card--back">
    <div class="back-brand">
      <div class="back-wordmark">Holloway Paving Service</div>
      <div class="back-phone">0418259730</div>
    </div>

    <div class="person">
      <h1 class="person-name">Mark Holloway</h1>
      <p class="person-role">Director</p>
    </div>

    <p class="address">
      <span class="address-suburb">Ashgrove</span><br>
      <span class="address-city">Kelsey, Tasmania 7090</span>
    </p>

    <ul class="contact-list">
      <li>
        <svg viewBox="0 0 12 12"><path d="M3 1 L5 3.5 L4 5 Q5.5 7.5 7 8 L8.5 7 L11 9 L9.5 11 Q4 10 1 3 Z" fill="var(--orange)"/></svg>
        +61 418 259 730
      </li>
      <li>
        <svg viewBox="0 0 12 12"><rect x="1" y="2.5" width="10" height="7" fill="none" stroke="var(--orange)" stroke-width="1.3"/><path d="M1 2.5 L6 6.5 L11 2.5" fill="none" stroke="var(--orange)" stroke-width="1.3"/></svg>
        markholloway@brightmail.com.au
      </li>
      <li>
        <svg viewBox="0 0 12 12"><circle cx="6" cy="6" r="5" fill="none" stroke="var(--orange)" stroke-width="1.2"/><ellipse cx="6" cy="6" rx="2.2" ry="5" fill="none" stroke="var(--orange)" stroke-width="1"/><path d="M1 6 H11" stroke="var(--orange)" stroke-width="1"/></svg>
        <span>www.<span class="accent">hollowaypaving</span>.com.au</span>
      </li>
      <li>
        <svg viewBox="0 0 12 12"><rect x="1.5" y="1.5" width="9" height="9" fill="none" stroke="var(--orange)" stroke-width="1.2"/><path d="M3.5 4.5 H8.5 M3.5 7 H7" stroke="var(--orange)" stroke-width="1"/></svg>
        ABN 62318470915
      </li>
    </ul>

    <div class="back-mark"></div>
  </section>
</main>
</body>
</html>
```